Corvane Spectrix Holdings - Business Cards

I would like a design developed using the logo (number 60387519) previously developed and attached. The information needs to include everything shown on the attached email title block, arranged to suit a business format. I would like a white background, with no other graphics added.
I need an editable version (e.g. MSWord) so I can change the name shown on the business card for others.

Target Market(s)

Mining & Heavy Manufacturing industries

Industry/Entity Type

Mining

Contact Information for Business Card

Refer to attached email title block in MSWord format for the details to be included.

Colors

Designer to choose colors to be used in the design.

Requirements
Must have
• White background, and fonts and text colour to match the unique font in the logo.
Nice to have
• the website address to be shown along the bottom of the card, as it is quite long.
Should not have
• Dark background, or unnecessary graphics

```html
<!DOCTYPE html>
<html lang="en">
<head>
<meta charset="utf-8">
<title>Corvane Spectrix Holdings – Business Card</title>
<link rel="stylesheet" href="https://fonts.googleapis.com/css2?family=Arimo:wght@400;700&display=swap">
<style>
  :root {
    --brand-blue: #0b7dc2;
    --text-grey: #7a7a7a;
    --card-white: #ffffff;
    --backdrop: #e4e5e7;
  }
  * { box-sizing: border-box; margin: 0; padding: 0; }
  html, body {
    width: 1200px;
    height: 815px;
    overflow: hidden;
    background: var(--backdrop);
    font-family: "Arimo", Arial, sans-serif;
  }
  .business-card {
    position: absolute;
    left: 110px;
    top: 127px;
    width: 980px;
    height: 560px;
    background: var(--card-white);
    box-shadow: 0 6px 24px rgba(0,0,0,0.12);
  }
  .holder-name {
    position: absolute;
    left: 62px;
    top: 58px;
    font-size: 42px;
    font-weight: 700;
    color: var(--brand-blue);
  }
  .holder-role {
    position: absolute;
    left: 64px;
    top: 108px;
    font-size: 24px;
    color: var(--text-grey);
  }
  .contact-list {
    position: absolute;
    left: 62px;
    top: 166px;
    list-style: none;
  }
  .contact-list li,
  .location-list li {
    display: flex;
    align-items: center;
    gap: 14px;
    font-size: 27px;
    color: var(--text-grey);
    height: 40px;
    white-space: nowrap;
  }
  .icon {
    width: 22px;
    height: 22px;
    flex: none;
  }
  .icon-spacer { width: 22px; flex: none; }
  .company-mark {
    position: absolute;
    left: 62px;
    top: 372px;
    display: flex;
    align-items: center;
    gap: 16px;
  }
  .company-mark .mark-dot {
    width: 46px;
    height: 46px;
    border-radius: 50%;
    background: var(--brand-blue);
    flex: none;
  }
  .company-mark .company-name {
    font-size: 30px;
    font-weight: 700;
    line-height: 1.1;
    color: var(--brand-blue);
    text-transform: uppercase;
    letter-spacing: 1px;
  }
  .location-list {
    position: absolute;
    left: 440px;
    top: 352px;
    list-style: none;
  }
  .location-list li { font-size: 25px; height: 36px; }
</style>
</head>
<body>
  <article class="business-card">
    <h1 class="holder-name">Renato (Nato) Vellis</h1>
    <p class="holder-role">Director</p>

    <ul class="contact-list">
      <li>
        <svg class="icon" viewBox="0 0 22 22" aria-hidden="true"><circle cx="11" cy="11" r="11" fill="#0b7dc2"/><rect x="5" y="7" width="12" height="8" fill="none" stroke="#fff" stroke-width="1.6"/><path d="M5 7l6 5 6-5" fill="none" stroke="#fff" stroke-width="1.6"/></svg>
        Email: renato.vellis@corvanespectrix.com.au
      </li>
      <li>
        <svg class="icon" viewBox="0 0 22 22" aria-hidden="true"><circle cx="11" cy="11" r="11" fill="#0b7dc2"/><rect x="7.5" y="4.5" width="7" height="13" rx="1.5" fill="#fff"/><rect x="9" y="6.5" width="4" height="7" fill="#0b7dc2"/></svg>
        Phone: +61 400 738 214
      </li>
      <li>
        <svg class="icon" viewBox="0 0 22 22" aria-hidden="true"><circle cx="11" cy="11" r="11" fill="#0b7dc2"/></svg>
        Messenger: cvs.renato.vellis
      </li>
    </ul>

    <div class="company-mark">
      <span class="mark-dot"></span>
      <span class="company-name">Corvane<br>Spectrix<br>Holdings</span>
    </div>

    <ul class="location-list">
      <li>
        <svg class="icon" viewBox="0 0 22 22" aria-hidden="true"><path d="M11 1c-4 0-7 3-7 7 0 5 7 12 7 12s7-7 7-12c0-4-3-7-7-7z" fill="#0b7dc2"/><circle cx="11" cy="8" r="2.6" fill="#fff"/></svg>
        PO BOX 41, Ferndale
      </li>
      <li><span class="icon-spacer"></span>NSW 2399, AUSTRALIA</li>
      <li>
        <svg class="icon" viewBox="0 0 22 22" aria-hidden="true"><circle cx="11" cy="11" r="10" fill="#0b7dc2"/><ellipse cx="11" cy="11" rx="4" ry="10" fill="none" stroke="#fff" stroke-width="1.4"/><path d="M1 11h20" stroke="#fff" stroke-width="1.4"/></svg>
        www.corvanespectrix.com.au
      </li>
      <li><span class="icon-spacer"></span>ABN 48 702 155 913</li>
    </ul>
  </article>
</body>
</html>
```